Kestrel Facilities Business Card Design

We would now like to design business cards with the new Kestrel Facilities logo

Target Market(s)

Professional

Industry/Entity Type

Professional services

Contact Information for Business Card

Employee name, title, phone number, email address, corporate office address and logo.

Font styles to use
Sans Serif

Colors
0054AA
0677BA
7BADD7
CADEEF
E8F1F8

Requirements
Must have
• My logo
Should not have
• any other pictures or images besides my logo

```html
<!DOCTYPE html>
<html lang="en">
<head>
<meta charset="utf-8">
<title>Kestrel Facilities Business Card</title>
<link rel="stylesheet" href="https://fonts.googleapis.com/css2?family=Montserrat:wght@600;700&family=Questrial&display=swap">
<style>
  :root {
    --brand-blue: #3477bd;
    --rule-blue: #2f6fb3;
    --band-grey: #8f9194;
    --ink: #1c1c1c;
    --paper: #ffffff;
    --stage: #b9b9b9;
  }
  * { box-sizing: border-box; margin: 0; padding: 0; }
  html, body { width: 1200px; height: 900px; overflow: hidden; }
  body {
    background: var(--stage);
    position: relative;
    font-family: "Questrial", sans-serif;
    color: var(--ink);
  }
  .card {
    position: absolute;
    width: 600px;
    height: 343px;
    border-radius: 26px;
    overflow: hidden;
    box-shadow: 0 6px 18px rgba(0,0,0,0.25);
  }
  .card-back {
    left: 110px;
    top: 70px;
    background: var(--brand-blue);
    display: flex;
    align-items: center;
    justify-content: center;
  }
  .card-front {
    left: 490px;
    top: 487px;
    background: var(--paper);
  }
  .wordmark {
    display: flex;
    align-items: center;
    gap: 14px;
    font-family: "Montserrat", sans-serif;
    font-weight: 700;
    letter-spacing: 0.02em;
    line-height: 1;
  }
  .wordmark-square {
    width: 34px;
    height: 34px;
  }
  .card-back .wordmark { color: var(--paper); font-size: 38px; }
  .card-back .wordmark-square { background: var(--paper); }
  .card-front .wordmark {
    position: absolute;
    left: 34px;
    top: 124px;
    color: var(--brand-blue);
    font-size: 25px;
    gap: 10px;
  }
  .card-front .wordmark-square { width: 26px; height: 26px; background: var(--brand-blue); }
  .divider {
    position: absolute;
    left: 318px;
    top: 62px;
    width: 2px;
    height: 168px;
    background: var(--rule-blue);
  }
  .details {
    position: absolute;
    left: 340px;
    top: 50px;
    width: 240px;
  }
  .person-name {
    font-family: "Montserrat", sans-serif;
    font-weight: 700;
    font-size: 20px;
    color: var(--brand-blue);
    letter-spacing: 0.01em;
  }
  .person-title { font-size: 15px; margin-top: 2px; }
  .address { font-size: 14px; line-height: 1.35; margin-top: 12px; }
  .contacts { list-style: none; margin-top: 10px; font-size: 14px; }
  .contacts li { display: flex; align-items: center; gap: 8px; line-height: 1.5; }
  .contacts svg { width: 13px; height: 13px; fill: var(--brand-blue); flex: none; }
  .bands { position: absolute; left: 0; bottom: 0; width: 600px; height: 80px; }
</style>
</head>
<body>
  <section class="card card-back" aria-label="Card back">
    <div class="wordmark"><span class="wordmark-square"></span>Kestrel Facilities</div>
  </section>

  <section class="card card-front" aria-label="Card front">
    <div class="wordmark"><span class="wordmark-square"></span>Kestrel Facilities</div>
    <div class="divider"></div>
    <div class="details">
      <p class="person-name">AMANI KOROS</p>
      <p class="person-title">Co-Founder</p>
      <p class="address">P.O Box 4410-00100<br>Nairobi, Kenya</p>
      <ul class="contacts">
        <li><svg viewBox="0 0 24 24"><path d="M6.6 10.8a15 15 0 0 0 6.6 6.6l2.2-2.2c.3-.3.7-.4 1-.2 1.1.4 2.3.6 3.6.6.6 0 1 .4 1 1V20c0 .6-.4 1-1 1A17 17 0 0 1 3 4c0-.6.4-1 1-1h3.5c.6 0 1 .4 1 1 0 1.3.2 2.5.6 3.6.1.3 0 .7-.2 1z"/></svg>+254-100-45210</li>
        <li><svg viewBox="0 0 24 24"><path d="M2 5h20v14H2zm2 2v.5l8 5 8-5V7z"/></svg>info@kestrelfacilities.com</li>
        <li><svg viewBox="0 0 24 24"><circle cx="12" cy="12" r="10"/></svg>www.kestrelfacilities.com</li>
      </ul>
    </div>
    <svg class="bands" viewBox="0 0 600 80" aria-hidden="true">
      <polygon points="412,22 600,22 600,80 392,80" fill="var(--band-grey)"/>
      <polygon points="0,52 404,52 394,80 0,80" fill="var(--brand-blue)"/>
    </svg>
  </section>
</body>
</html>
```